innovative design Cafe Menu

looking for an innovative design for a food menu for a coffee shop and take away restaurant.

Target Market(s)

Canada

Requirements
Must have
• innovative design and easy to navigate and reading

```html
<!DOCTYPE html>
<html lang="en">
<head>
<meta charset="utf-8">
<title>Rowan's Cafe Menu</title>
<link href="https://fonts.googleapis.com/css2?family=Merriweather:wght@400;700&display=swap" rel="stylesheet">
<style>
:root{
  --green-deep:#064d22;
  --green-bar:#4fa34a;
  --green-title:#3f9a3a;
  --orange:#f5a623;
  --ink:#1d1d1d;
  --maroon:#6b1f24;
  --photo-wood:#3a3038;
  --photo-wings:#e7dccb;
  --photo-cake:#e9e4de;
  --paper:#ffffff;
}
*{margin:0;padding:0;box-sizing:border-box}
html,body{width:848px;height:1200px;overflow:hidden;background:var(--paper)}
.menu{position:relative;width:848px;height:1200px;overflow:hidden;font-family:'Merriweather',Georgia,serif;color:var(--ink)}
.backdrop{position:absolute;inset:0}
.brand{position:absolute;left:488px;top:52px;width:240px;text-align:center;font-weight:700;color:var(--maroon);font-size:34px;line-height:1.15}
.section-bar{position:absolute;height:23px;background:var(--green-bar);color:#fff;font-weight:700;font-size:13px;line-height:23px;padding-left:8px}
.sides-bar{left:37px;top:674px;width:368px}
.wraps-bar{left:437px;top:624px;width:367px}
.dessert-bar{left:38px;top:1032px;width:368px}
.item{position:absolute;width:347px}
.col-left .item{left:45px}
.col-right .item{left:444px}
.item-row{display:flex;align-items:baseline;gap:4px}
.item-name{color:var(--green-title);font-weight:700;font-size:13.5px;white-space:nowrap}
.item-dots{flex:1;border-bottom:1px dotted #444;transform:translateY(-3px)}
.item-price{font-size:12.5px;white-space:nowrap}
.item-desc{font-size:11.3px;line-height:16px;margin-top:1px;white-space:nowrap}
</style>
</head>
<body>
<div class="menu">
  <svg class="backdrop" width="848" height="1200" viewBox="0 0 848 1200">
    <path role="img" aria-label="Photo of falafel wraps with salad and dip on a wooden board" fill="var(--photo-wood)" d="M0,195 C60,150 150,105 210,105 C300,105 360,190 430,190 C520,190 620,150 700,160 C770,168 820,150 848,155 L848,600 C790,605 760,560 700,545 C620,525 560,545 480,540 C380,535 300,500 250,440 C210,390 180,290 120,265 C70,245 30,270 0,260 Z"/>
    <path d="M195,105 C280,120 360,210 450,225 C560,240 650,190 760,205 C810,212 835,225 848,235" fill="none" stroke="#fff" stroke-width="1.5"/>
    <path d="M150,360 C200,470 260,520 360,530 C480,545 620,540 700,560 C780,580 820,570 848,560" fill="none" stroke="#fff" stroke-width="1.5"/>

    <rect role="img" aria-label="Photo of grilled chicken wings with tomatoes and lettuce" x="10" y="440" width="375" height="215" rx="18" fill="var(--photo-wings)"/>

    <path fill="var(--green-deep)" d="M0,0 L418,0 C400,60 360,95 300,95 C230,95 170,100 120,130 C80,155 40,185 0,200 Z"/>
    <path d="M418,0 C405,50 370,90 300,92 C220,95 150,92 100,130 C60,160 30,180 0,192" fill="none" stroke="var(--orange)" stroke-width="4"/>

    <g fill="#fff">
      <circle cx="270" cy="7" r="2.5"/><circle cx="295" cy="7" r="2.5"/><circle cx="320" cy="7" r="2.5"/><circle cx="345" cy="7" r="2.5"/><circle cx="370" cy="7" r="2.5"/>
      <circle cx="270" cy="25" r="2.5"/><circle cx="295" cy="25" r="2.5"/><circle cx="320" cy="25" r="2.5"/><circle cx="345" cy="25" r="2.5"/><circle cx="370" cy="25" r="2.5"/>
      <circle cx="270" cy="42" r="2.5"/><circle cx="295" cy="42" r="2.5"/><circle cx="320" cy="42" r="2.5"/><circle cx="345" cy="42" r="2.5"/><circle cx="370" cy="42" r="2.5"/>
      <circle cx="270" cy="60" r="2.5"/><circle cx="295" cy="60" r="2.5"/><circle cx="320" cy="60" r="2.5"/><circle cx="345" cy="60" r="2.5"/><circle cx="370" cy="60" r="2.5"/>
      <circle cx="218" cy="450" r="2.5"/><circle cx="243" cy="450" r="2.5"/><circle cx="267" cy="450" r="2.5"/><circle cx="292" cy="450" r="2.5"/><circle cx="316" cy="450" r="2.5"/>
      <circle cx="218" cy="468" r="2.5"/><circle cx="243" cy="468" r="2.5"/><circle cx="267" cy="468" r="2.5"/><circle cx="292" cy="468" r="2.5"/><circle cx="316" cy="468" r="2.5"/>
      <circle cx="218" cy="486" r="2.5"/><circle cx="243" cy="486" r="2.5"/><circle cx="267" cy="486" r="2.5"/><circle cx="292" cy="486" r="2.5"/><circle cx="316" cy="486" r="2.5"/>
      <circle cx="218" cy="504" r="2.5"/><circle cx="243" cy="504" r="2.5"/><circle cx="267" cy="504" r="2.5"/><circle cx="292" cy="504" r="2.5"/><circle cx="316" cy="504" r="2.5"/>
      <circle cx="218" cy="522" r="2.5"/><circle cx="243" cy="522" r="2.5"/><circle cx="267" cy="522" r="2.5"/><circle cx="292" cy="522" r="2.5"/><circle cx="316" cy="522" r="2.5"/>
      <circle cx="218" cy="540" r="2.5"/><circle cx="243" cy="540" r="2.5"/><circle cx="267" cy="540" r="2.5"/><circle cx="292" cy="540" r="2.5"/><circle cx="316" cy="540" r="2.5"/>
      <circle cx="770" cy="177" r="2.5"/><circle cx="796" cy="177" r="2.5"/><circle cx="822" cy="177" r="2.5"/>
      <circle cx="770" cy="196" r="2.5"/><circle cx="796" cy="196" r="2.5"/><circle cx="822" cy="196" r="2.5"/>
      <circle cx="770" cy="215" r="2.5"/><circle cx="796" cy="215" r="2.5"/><circle cx="822" cy="215" r="2.5"/>
      <circle cx="770" cy="234" r="2.5"/><circle cx="796" cy="234" r="2.5"/><circle cx="822" cy="234" r="2.5"/>
      <circle cx="770" cy="253" r="2.5"/><circle cx="796" cy="253" r="2.5"/><circle cx="822" cy="253" r="2.5"/>
      <circle cx="770" cy="272" r="2.5"/><circle cx="796" cy="272" r="2.5"/><circle cx="822" cy="272" r="2.5"/>
    </g>
    <g fill="#d6d6d6">
      <circle cx="13" cy="311" r="2.5"/><circle cx="39" cy="311" r="2.5"/><circle cx="65" cy="311" r="2.5"/>
      <circle cx="13" cy="330" r="2.5"/><circle cx="39" cy="330" r="2.5"/><circle cx="65" cy="330" r="2.5"/>
      <circle cx="13" cy="349" r="2.5"/><circle cx="39" cy="349" r="2.5"/><circle cx="65" cy="349" r="2.5"/>
      <circle cx="13" cy="368" r="2.5"/><circle cx="39" cy="368" r="2.5"/><circle cx="65" cy="368" r="2.5"/>
      <circle cx="13" cy="387" r="2.5"/><circle cx="39" cy="387" r="2.5"/><circle cx="65" cy="387" r="2.5"/>
      <circle cx="13" cy="405" r="2.5"/><circle cx="39" cy="405" r="2.5"/><circle cx="65" cy="405" r="2.5"/>
    </g>

    <rect role="img" aria-label="Photo of a slice of berry cheesecake on a dark plate" x="452" y="958" width="300" height="242" rx="14" fill="var(--photo-cake)"/>
    <path fill="var(--green-deep)" d="M460,1200 C530,1175 600,1140 660,1070 C720,1000 760,945 848,930 L848,1200 Z"/>
    <path d="M575,1200 C640,1180 690,1150 740,1090 C780,1040 810,1020 848,1010" fill="none" stroke="var(--orange)" stroke-width="3.5"/>
    <path d="M470,1160 C560,1160 640,1120 700,1060 C760,1000 800,990 848,975" fill="none" stroke="#fff" stroke-width="1.5"/>
  </svg>

  <div class="brand">Rowan's<br>Cafe</div>

  <div class="col-left">
    <div class="section-bar sides-bar">Sides</div>
    <div class="item" style="top:705px"><div class="item-row"><span class="item-name">Crispy French Fries</span><span class="item-dots"></span><span class="item-price">$ 2.00</span></div><p class="item-desc">Crispy Flavoured Frech Fries</p></div>
    <div class="item" style="top:746px"><div class="item-row"><span class="item-name">French Fries</span><span class="item-dots"></span><span class="item-price">$ 1.75</span></div><p class="item-desc">Straight Cut Fries</p></div>
    <div class="item" style="top:788px"><div class="item-row"><span class="item-name">Buffalo Chiken Wings 5 Pcs.</span><span class="item-dots"></span><span class="item-price">$ 5.50</span></div><p class="item-desc">Juicy from inside crispy from outside<br>for of flavours</p></div>
    <div class="item" style="top:845px"><div class="item-row"><span class="item-name">Buffalo Chiken Wings 10 Pcs.</span><span class="item-dots"></span><span class="item-price">$ 10.00</span></div><p class="item-desc">Juicy from inside crispy from outside<br>for of flavours</p></div>
    <div class="item" style="top:903px"><div class="item-row"><span class="item-name">Honey Garlic Chicken Wings</span><span class="item-dots"></span><span class="item-price">$ 10.00</span></div></div>
    <div class="item" style="top:929px"><div class="item-row"><span class="item-name">Fried Calamari</span><span class="item-dots"></span><span class="item-price">$ 7.99</span></div></div>
    <div class="item" style="top:954px"><div class="item-row"><span class="item-name">Oriental Rice</span><span class="item-dots"></span><span class="item-price">$ 2.00</span></div><p class="item-desc">Flavourful rice short grain rice cooked<br>with onion, garlic and tomato</p></div>

    <div class="section-bar dessert-bar">Dessert</div>
    <div class="item" style="top:1062px"><div class="item-row"><span class="item-name">Cheesecake</span><span class="item-dots"></span><span class="item-price">$ 4.00</span></div><p class="item-desc">New York style cheesecake with<br>different topic (Caramel/Strawberry)</p></div>
    <div class="item" style="top:1120px"><div class="item-row"><span class="item-name">Lutce Cheesecake</span><span class="item-dots"></span><span class="item-price">$ 4.00</span></div></div>
  </div>

  <div class="col-right">
    <div class="section-bar wraps-bar">Wraps</div>
    <div class="item" style="top:655px"><div class="item-row"><span class="item-name">Crispy Chicken</span><span class="item-dots"></span><span class="item-price">$ 6.99</span></div><p class="item-desc">Tender juicy peice of chicken marinated with our<br>im-house marination fried with a crispy tempura batter<br>serve with lettuce tomato cucumber pickles and mayo</p></div>
    <div class="item" style="top:728px"><div class="item-row"><span class="item-name">Falafel</span><span class="item-dots"></span><span class="item-price">$ 4.99</span></div><p class="item-desc">Falafel is a deep-fried ball made from ground chickpeas<br>and fava beans. Served wrapped in a tortilla with<br>tahini sauce, lettuce, tomato and pickles</p></div>
    <div class="item" style="top:802px"><div class="item-row"><span class="item-name">Grilled Chicken</span><span class="item-dots"></span><span class="item-price">$ 6.99</span></div><p class="item-desc">Tender juicy chicken pics marinated overnight was our<br>special marination made in the house laid over garlic<br>mayo lettuce and tomato and pickel wrap in tortilla</p></div>
    <div class="item" style="top:875px"><div class="item-row"><span class="item-name">Kofta</span><span class="item-dots"></span><span class="item-price">$ 6.99</span></div><p class="item-desc">Barbeque ground beef our seasoning serve was the<br>tahini sauce pickle, lettuce and tomato</p></div>
  </div>
</div>
</body>
</html>
```